Brell Stone Company Business Cards

Front and Back Business Card - logo and text setup - cool design. I need workable photoshop or illustrator files so I can setup each employee card with design that is created
Updates

Hi everyone, thank you for the great entries. Please no more white and blue cards - there are so many already - black and silver only now please. thanks!

Target Market(s)

Construction Industry - Facility Managers

Industry/Entity Type

Construction

Contact Information for Business Card

I really like contemporary simplistic looks - clean neat....not opposed to seeing some black backrounds

Requirements
Must have
• Logo/website address with design on front only - www.brellstone-example.com (logo attached)
• Back:
• Name/Title/Company Address/Phone/email address
Nice to have
• Cool design
Should not have
• Nothing gimmicky like Fire or Water - since we are a Fire Protection company - it has all been done

```html
<!DOCTYPE html>
<html lang="en">
<head>
<meta charset="utf-8">
<title>Brell Stone Company — Business Cards</title>
<link href="https://fonts.googleapis.com/css2?family=Quicksand:wght@400;500;700&display=swap" rel="stylesheet">
<style>
  :root {
    --backdrop: #c41e2a;
    --card: #141416;
    --silver: #c9ccd1;
    --silver-bright: #e6e8eb;
    --silver-dim: #9a9ea5;
    --edge: #8d9096;
  }
  * { margin: 0; padding: 0; box-sizing: border-box; }
  html, body { width: 1200px; height: 1050px; overflow: hidden; }
  body {
    background: var(--backdrop);
    font-family: "Quicksand", sans-serif;
    position: relative;
  }
  .card {
    position: absolute;
    left: 255px;
    width: 690px;
    height: 394px;
    background: var(--card);
    border-bottom: 5px solid var(--edge);
    box-shadow: 0 14px 30px rgba(40, 0, 0, 0.45);
  }
  .card--back { top: 70px; }
  .card--front { top: 560px; }

  .accent-bar {
    position: absolute;
    left: 0; top: 62px;
    width: 12px; height: 46px;
    background: var(--silver);
  }
  .holder { position: absolute; left: 52px; top: 64px; }
  .holder__name {
    color: var(--silver-bright);
    font-weight: 700;
    font-size: 25px;
    letter-spacing: 1.5px;
    text-transform: uppercase;
  }
  .holder__title { color: var(--silver-dim); font-size: 15px; margin-top: 4px; }

  .contact { position: absolute; left: 36px; top: 150px; list-style: none; }
  .contact__item {
    display: flex; align-items: center; gap: 12px;
    color: var(--silver); font-size: 16px; margin-bottom: 10px;
  }
  .contact__icon { width: 20px; height: 20px; flex: none; }

  .wordmark {
    display: flex; align-items: center; gap: 12px;
    color: var(--silver-bright); font-weight: 700;
    white-space: nowrap;
  }
  .wordmark__square { background: var(--silver); flex: none; }
  .card--back .wordmark { position: absolute; right: 40px; top: 62px; font-size: 40px; }
  .card--back .wordmark__square { width: 20px; height: 20px; }
  .card--front .wordmark {
    position: absolute; left: 0; right: 0; top: 160px;
    justify-content: center; font-size: 62px;
  }
  .card--front .wordmark__square { width: 30px; height: 30px; }

  .address {
    position: absolute; right: 40px; bottom: 38px;
    text-align: right; font-style: normal;
    color: var(--silver); font-size: 16px; line-height: 1.5;
  }
</style>
</head>
<body>
  <section class="card card--back" aria-label="Business card back">
    <div class="accent-bar"></div>
    <div class="holder">
      <p class="holder__name">Dana Whitfield</p>
      <p class="holder__title">Director</p>
    </div>
    <ul class="contact">
      <li class="contact__item">
        <svg class="contact__icon" viewBox="0 0 20 20" aria-hidden="true"><circle cx="10" cy="10" r="10" fill="#c9ccd1"/><path d="M6.5 5.5l2 0 1 2.5-1.3 1a6 6 0 0 0 2.8 2.8l1-1.3 2.5 1v2a1 1 0 0 1-1 1A8.5 8.5 0 0 1 5.5 6.5a1 1 0 0 1 1-1z" fill="#141416"/></svg>
        (555) 014-2290
      </li>
      <li class="contact__item">
        <svg class="contact__icon" viewBox="0 0 20 20" aria-hidden="true"><circle cx="10" cy="10" r="10" fill="#c9ccd1"/><rect x="5" y="6.5" width="10" height="7" rx="1" fill="#141416"/><path d="M5.5 7l4.5 3.5L14.5 7" fill="none" stroke="#c9ccd1" stroke-width="1"/></svg>
        info@brellstone-example.com
      </li>
      <li class="contact__item">
        <svg class="contact__icon" viewBox="0 0 20 20" aria-hidden="true"><circle cx="10" cy="10" r="10" fill="#c9ccd1"/><circle cx="10" cy="10" r="5" fill="none" stroke="#141416" stroke-width="1.2"/><path d="M5 10h10M10 5c-2.5 3-2.5 7 0 10M10 5c2.5 3 2.5 7 0 10" fill="none" stroke="#141416" stroke-width="1"/></svg>
        www.brellstone-example.com
      </li>
    </ul>
    <div class="wordmark"><span class="wordmark__square"></span>Brell Stone</div>
    <address class="address">48 Harbor Point Road<br>Millbrook, NY 10000</address>
  </section>

  <section class="card card--front" aria-label="Business card front">
    <div class="wordmark"><span class="wordmark__square"></span>Brell Stone</div>
  </section>
</body>
</html>
```